Ridgeline Journeys business card

please see website
www.ridgelinejourneys.comau

info needed on card
Curtis Halvey
Ph
email
Adventure Riding GPS trails

please use my logo and colours off my site

Curtis Halvey
curtis@ridgelinejourneys.com

```html
<!DOCTYPE html>
<html lang="en">
<head>
<meta charset="utf-8">
<title>Ridgeline Journeys – Business Card</title>
<link rel="stylesheet" href="https://fonts.googleapis.com/css2?family=Arimo:wght@400;700&display=swap">
<style>
  :root {
    --stage: #141414;
    --card-white: #ffffff;
    --brand-yellow: #f9ec4f;
    --mark-yellow: #f6d81c;
    --ink: #0d0d0d;
  }
  * { box-sizing: border-box; margin: 0; padding: 0; }
  html, body {
    width: 1189px;
    height: 1200px;
    overflow: hidden;
    background: var(--stage);
    font-family: "Arimo", Arial, sans-serif;
    color: var(--ink);
  }
  .card {
    position: absolute;
    left: 140px;
    width: 918px;
    height: 524px;
    background: var(--card-white);
    overflow: hidden;
  }
  .card--front { top: 45px; }
  .card--back { top: 623px; }
  .card__art { position: absolute; inset: 0; }
  .brand {
    position: absolute;
    font-weight: 700;
    font-size: 66px;
    line-height: 74px;
    color: var(--ink);
    letter-spacing: 0.5px;
  }
  .card--front .brand { left: 403px; top: 92px; }
  .card--back .brand { left: 395px; top: 198px; font-size: 70px; line-height: 80px; }
  .holder {
    position: absolute;
    left: 41px;
    top: 440px;
    font-size: 49px;
    font-weight: 400;
    line-height: 56px;
  }
  .divider {
    position: absolute;
    left: 403px;
    top: 408px;
    width: 2px;
    height: 102px;
    background: var(--ink);
  }
  .contact {
    position: absolute;
    left: 420px;
    list-style: none;
  }
  .contact__item {
    display: flex;
    align-items: center;
    height: 44px;
    font-size: 26px;
  }
  .contact__icon { width: 22px; height: 22px; margin-right: 24px; flex: none; }
  .contact { top: 416px; }
</style>
</head>
<body>

<section class="card card--front" aria-label="Business card front">
  <svg class="card__art" viewBox="0 0 918 524" aria-hidden="true">
    <path d="M0,200 Q405,643 918,98 L918,524 L0,524 Z" fill="var(--brand-yellow)"/>
    <path d="M0,94 Q458,601 811,216 Q458,536 0,160 Z" fill="var(--ink)"/>
    <circle cx="261" cy="151" r="96" fill="var(--mark-yellow)"/>
  </svg>
  <h1 class="brand">Ridgeline<br>Journeys</h1>
  <p class="holder">Curtis Halvey</p>
  <span class="divider"></span>
  <ul class="contact">
    <li class="contact__item">
      <svg class="contact__icon" viewBox="0 0 22 22" aria-hidden="true">
        <rect width="22" height="22" rx="2" fill="var(--ink)"/>
        <path d="M5 9 Q11 4 17 9 L15 11 L13 9 L9 9 L7 11 Z M7 12 H15 V16 H7 Z" fill="#fff"/>
      </svg>
      <span>curtis@ridgelinejourneys.com</span>
    </li>
    <li class="contact__item">
      <svg class="contact__icon" viewBox="0 0 22 22" aria-hidden="true">
        <rect width="22" height="22" rx="2" fill="var(--ink)"/>
        <circle cx="11" cy="11" r="7" fill="#fff"/>
        <path d="M8 7 Q11 9 10 12 Q8 13 9 16 M13 6 Q12 9 15 10 Q16 13 14 15" stroke="var(--ink)" stroke-width="1.6" fill="none"/>
      </svg>
      <span>www.ridgelinejourneys.com.au</span>
    </li>
  </ul>
</section>

<section class="card card--back" aria-label="Business card back">
  <svg class="card__art" viewBox="0 0 918 524" aria-hidden="true">
    <circle cx="220" cy="258" r="106" fill="var(--mark-yellow)"/>
  </svg>
  <h2 class="brand">Ridgeline<br>Journeys</h2>
</section>

</body>
</html>
```